Design Website Templates for Photographers for Lumera Inc. (trylumera.example)

Lumera Inc. is a generative website company for wedding photographers.
We are seeking new photography website design inspirations for the next template to be offered on our platform. The catch is you must use the same data for your designs. You also must use all of the data somewhere in the design. You cannot add new content besides the data available. If you wish to add any elements It will be hardcoded and must be universally fitting for many different photographers. We recommend not using any hardcoded test.
Don't be afraid to be creative! Although the most important element of a photographers website is the photos, we are looking for unique and out-of-the-box designs for the actual site as well.
Here is the User generated data available to you:
- 4 Hero Images Landscape, 4 Hero Images Portrait
- Tagline “destination photographer based in Maui, Hawaii”
- “About Photo” of the photographer
- “About” Biography Text
- The design can use up to 3 colors + background color and 2 fonts
- 9 Gallery images
- 3 Packages/services that include landscape/portrait images, a price, a title and text
- Testimonials made up of an image, text and text for the name of testimonial giver
See some examples of our current website designs attached. You can use any of the data you see in the designs.
Updates
We are looking for designs that are less feminine and are more neutral in color and fonts. Currently our templates are more oriented towards feminine photographers. We want to have designs that speak to diverse audiences. We thank everyone for submitting and are reviewing the designs.
Number of Pages Required
1 page
Look and feel
Each slider illustrates characteristics of the customer's brand and the style your logo design should communicate.

```html
<!DOCTYPE html>
<html lang="en">
<head>
<meta charset="utf-8">
<title>Lumera — Destination Photographer</title>
<link rel="stylesheet" href="https://fonts.googleapis.com/css2?family=Cinzel:wght@600;700&family=Poppins:wght@400;500;600&display=swap">
<style>
:root{
  --gold:#efb024;
  --gold-deep:#d99612;
  --ink:#222222;
  --text:#555555;
  --cream:#f8f4ee;
  --white:#ffffff;
  --footer:#262626;
  --footer-line:#3a3a3a;
  --footer-text:#cfcfcf;
}
*{box-sizing:border-box;margin:0;padding:0}
html,body{width:1200px;height:4332px;overflow:hidden}
body{position:relative;background:var(--white);font-family:"Poppins",sans-serif;color:var(--text)}
.abs{position:absolute}
.serif{font-family:"Cinzel",serif}
.photo{position:absolute;box-shadow:0 6px 18px rgba(0,0,0,.18);border:6px solid var(--white)}

/* header & hero */
.hero{left:0;top:0;width:1200px;height:700px;
  background:
    radial-gradient(ellipse 260px 340px at 860px 340px,rgba(238,226,212,.55),rgba(238,226,212,0) 70%),
    radial-gradient(ellipse 700px 260px at 600px 470px,rgba(240,170,90,.55),rgba(240,170,90,0) 70%),
    linear-gradient(180deg,#2c2220 0%,#4b3a33 22%,#8a6a52 45%,#c89566 58%,#7d5639 72%,#3f2c20 100%)}
.hero-shade{left:0;top:0;width:1200px;height:140px;background:linear-gradient(180deg,rgba(0,0,0,.35),rgba(0,0,0,0))}
.logo{left:112px;top:38px;font-size:42px;font-weight:600;letter-spacing:4px;color:var(--white)}
.nav{left:444px;top:56px;display:flex;gap:22px;font-size:15px;font-weight:500;color:var(--white)}
.nav .active{color:var(--gold);border-bottom:2px solid var(--gold);padding-bottom:4px}
.btn{background:var(--gold);color:var(--white);font-weight:600;font-size:14px;border-radius:22px;text-align:center;letter-spacing:.5px}
.signup{left:968px;top:44px;width:118px;height:40px;line-height:40px}
.hero-title{left:200px;top:262px;width:760px;text-align:center;font-size:37px;line-height:50px;color:var(--white);letter-spacing:1px;text-shadow:0 2px 10px rgba(0,0,0,.35)}
.cta{left:536px;top:376px;width:138px;height:42px;line-height:42px}
.social-rail{left:1124px;top:110px;display:flex;flex-direction:column;gap:18px}
.social-rail span{width:28px;height:28px;border-radius:50%;background:rgba(255,255,255,.22);border:1.5px solid rgba(255,255,255,.85);display:block}
.dots{left:980px;top:602px;display:flex;gap:12px}
.dots span{width:10px;height:10px;border-radius:50%;background:rgba(255,255,255,.7)}
.dots .on{background:var(--white);box-shadow:0 0 0 3px rgba(255,255,255,.4)}
.down{left:556px;top:578px;width:88px;height:88px;border-radius:50%;background:var(--white);box-shadow:0 4px 14px rgba(0,0,0,.2)}

/* about */
.about-photo{left:112px;top:752px;width:450px;height:450px;border-radius:50%;
  background:
    radial-gradient(circle at 62% 40%,rgba(232,212,196,.8),rgba(232,212,196,0) 35%),
    radial-gradient(circle at 25% 70%,rgba(150,90,60,.7),rgba(150,90,60,0) 40%),
    linear-gradient(120deg,#d9c4ad 0%,#8a6650 40%,#4b382d 70%,#cbb49c 100%)}
.section-title{font-size:40px;font-weight:700;color:var(--ink);letter-spacing:2px}
.section-title em{font-style:normal;color:var(--gold)}
.about-title{left:636px;top:770px}
.about-text{left:636px;top:850px;width:460px;font-size:14.5px;line-height:26px}
.about-text p+p{margin-top:20px}
.read-more{left:636px;top:1116px;width:134px;height:44px;line-height:44px}

/* gallery */
.gallery-bg{left:0;top:1340px;width:1200px;height:1312px;background:var(--cream)}
.gallery-title{left:0;top:1436px;width:1200px;text-align:center}

/* packages */
.packages-bg{left:0;top:2652px;width:1200px;height:380px;background:linear-gradient(180deg,#c98c18,var(--gold) 60%,#f3c252)}
.packages-title{left:0;top:2746px;width:1200px;text-align:center;color:var(--white)}
.pkg-name{font-size:17px;font-weight:600;color:var(--ink);text-align:center;width:308px;letter-spacing:.5px}
.pkg-price{font-size:16px;font-weight:600;color:var(--gold);text-align:center;width:308px}

/* testimonials */
.testi-title{left:0;top:3368px;width:1200px;text-align:center}
.card{position:absolute;top:3456px;width:308px;height:280px;background:var(--white);box-shadow:0 6px 22px rgba(0,0,0,.12);border-radius:8px;padding:92px 28px 0}
.avatar{position:absolute;left:122px;top:20px;width:64px;height:64px;border-radius:50%;border:3px solid var(--gold)}
.card p{font-size:13px;line-height:21px;color:var(--text)}
.card .who{margin-top:12px;font-size:14px;font-weight:600;color:var(--ink)}
.stars{margin-top:4px;color:var(--gold);font-size:12px;letter-spacing:2px}
.quote{position:absolute;right:24px;bottom:40px;font-family:"Cinzel",serif;font-size:90px;line-height:1;color:#e6e6e6}
.arrow-btn{position:absolute;top:3580px;width:34px;height:34px;border-radius:50%;background:#eeeeee}

/* footer */
.footer-area{color:var(--footer-text)}
.footer{left:0;top:3876px;width:1200px;height:456px;background:var(--footer)}
.f-logo{left:112px;top:3940px;font-size:42px;font-weight:600;letter-spacing:4px;color:var(--white)}
.to-top{left:994px;top:3964px;font-size:14px;font-weight:600;color:var(--white)}
.f-rule{left:112px;top:4020px;width:976px;height:1px;background:var(--footer-line)}
.f-head{font-size:15px;font-weight:600;color:var(--white);letter-spacing:.5px}
.f-list{font-size:13px;line-height:29px;list-style:none;color:var(--footer-text)}
.f-list li::before{content:"";display:inline-block;width:7px;height:7px;border-radius:50%;background:var(--gold);margin-right:12px;vertical-align:middle}
.contact-row{display:flex;gap:14px;font-size:13px;line-height:20px;margin-bottom:12px;color:var(--footer-text)}
.contact-row svg{flex:none;margin-top:3px}
.f-social{display:flex;gap:10px}
.f-social span{width:32px;height:32px;border-radius:50%;background:#3a3a3a;border:1.5px solid var(--footer-text)}
.bottom-rule{left:0;top:4272px;width:1200px;height:1px;background:var(--footer-line)}
.copyright{left:0;top:4290px;width:1200px;text-align:center;font-size:12.5px;color:#bdbdbd}
</style>
</head>
<body>

<header>
  <div class="abs hero" role="img" aria-label="Hero photo: bride and groom embracing on a hilltop at sunset"></div>
  <div class="abs hero-shade"></div>
  <div class="abs logo">LUMERA</div>
  <nav class="abs nav">
    <span class="active">HOME</span><span>ABOUT</span><span>SERVICES</span><span>GALLERY</span><span>PRICING</span><span>CONTACT US</span>
  </nav>
  <div class="abs btn signup">&#9679;&nbsp; SIGN UP</div>
  <h1 class="abs hero-title serif">DESTINATION PHOTOGRAPHER<br>BASED IN MAUI, HAWAII</h1>
  <div class="abs btn cta">GET STARTED</div>
  <div class="abs social-rail"><span></span><span></span><span></span><span></span></div>
  <svg class="abs" style="left:0;top:500px" width="1200" height="210" viewBox="0 0 1200 210">
    <path d="M0 120 C250 30 420 150 600 130 C820 105 980 40 1200 60 L1200 210 L0 210Z" fill="var(--gold)"/>
    <path d="M0 150 C250 70 420 175 600 158 C820 138 980 80 1200 95 L1200 210 L0 210Z" fill="var(--white)"/>
  </svg>
  <div class="abs dots"><span></span><span></span><span class="on"></span><span></span><span></span></div>
  <div class="abs down">
    <svg width="88" height="88" viewBox="0 0 88 88"><path d="M32 38 L44 50 L56 38" fill="none" stroke="var(--ink)" stroke-width="4" stroke-linecap="round" stroke-linejoin="round"/></svg>
  </div>
</header>

<section class="about">
  <div class="abs about-photo" role="img" aria-label="Photographer holding a camera, reflected in a mirror"></div>
  <h2 class="abs section-title serif about-title">ABOUT <em>US</em></h2>
  <div class="abs about-text">
    <p>Lorem ipsum dolor sit amet, consectetur adipiscing elit, sed do eiusmod tempor incididunt ut labore et dolore magna aliqua. Ut enim ad minim veniam, quis nostrud exercitation ullamco laboris nisi ut aliquip ex ea commodo consequat duis aute irure dolor in reprehenderit in voluptate velit.</p>
    <p>Lorem ipsum dolor sit amet, consectetur adipiscing elit, sed do eiusmod tempor incididunt ut labore et dolore magna aliqua. Ut enim ad minim veniam.</p>
  </div>
  <div class="abs btn read-more">READ MORE</div>
</section>

<section class="gallery">
  <div class="abs gallery-bg"></div>
  <h2 class="abs section-title serif gallery-title">OUR <em>GALLERY</em></h2>
  <div class="photo" style="left:112px;top:1552px;width:308px;height:226px;background:radial-gradient(ellipse at 55% 55%,#f2ece4 0%,#cbbba8 30%,rgba(203,187,168,0) 60%),linear-gradient(160deg,#8a7866,#5a4b40 50%,#b8a590)" role="img" aria-label="Couple laughing among wedding guests"></div>
  <div class="photo" style="left:112px;top:1806px;width:308px;height:424px;background:radial-gradient(ellipse at 45% 65%,#efe9e1 0%,#bfb09d 28%,rgba(191,176,157,0) 55%),linear-gradient(180deg,#5f6b45 0%,#8a8a5c 35%,#6b5d4b 70%,#3e3631)" role="img" aria-label="Bride and groom smiling in a garden"></div>
  <div class="photo" style="left:112px;top:2258px;width:308px;height:290px;background:radial-gradient(ellipse at 50% 60%,#ece5da 0%,#c7b7a3 28%,rgba(199,183,163,0) 55%),linear-gradient(180deg,#7f9a7e 0%,#a9bca5 40%,#8b7d6b 75%,#5b5148)" role="img" aria-label="Couple holding hands outdoors"></div>
  <div class="photo" style="left:444px;top:1552px;width:308px;height:400px;background:radial-gradient(ellipse at 35% 65%,#f4efe9 0%,#d8cbbb 25%,rgba(216,203,187,0) 50%),radial-gradient(ellipse at 70% 40%,#2f2a2a 0%,rgba(47,42,42,0) 45%),linear-gradient(160deg,#b59f86,#6d5646 55%,#3c302a)" role="img" aria-label="Groom kissing bride"></div>
  <div class="photo" style="left:444px;top:1966px;width:308px;height:264px;background:radial-gradient(ellipse at 50% 70%,#5e5248 0%,rgba(94,82,72,0) 22%),linear-gradient(180deg,#f1ece4 0%,#e2d8ca 45%,#c6b79f 75%,#9b8a70)" role="img" aria-label="Couple walking in a misty field"></div>
  <div class="photo" style="left:444px;top:2312px;width:308px;height:236px;background:radial-gradient(ellipse at 50% 20%,#fbf3e6 0%,rgba(251,243,230,0) 50%),linear-gradient(180deg,#e9d7bd 0%,#c9a57d 45%,#8a6a4e 75%,#5a4637)" role="img" aria-label="Couple under a draped reception tent"></div>
  <div class="photo" style="left:776px;top:1552px;width:308px;height:304px;background:linear-gradient(180deg,#9fc1dc 0%,#cfe0ea 35%,#8ea3ad 50%,#6f7e7f 62%,#b6aa99 80%,#857766)" role="img" aria-label="Waterfront ceremony with city skyline"></div>
  <div class="photo" style="left:776px;top:1880px;width:308px;height:350px;background:radial-gradient(ellipse at 45% 55%,#eeeae4 0%,rgba(238,234,228,0) 22%),linear-gradient(180deg,#b9bdb8 0%,#9aa49c 35%,#5d6b61 60%,#3a403b 85%,#2b2f2c)" role="img" aria-label="Couple dancing on a rocky shore"></div>
  <div class="photo" style="left:776px;top:2256px;width:308px;height:292px;background:radial-gradient(ellipse at 50% 35%,#6b8a5a 0%,rgba(107,138,90,0) 25%),linear-gradient(180deg,#f4f2ec 0%,#e3ded3 45%,#cfc6b5 75%,#a59b89)" role="img" aria-label="Ceremony in a white glass pavilion"></div>
</section>

<section class="packages">
  <div class="abs packages-bg" role="img" aria-label="Warm golden backdrop photo"></div>
  <h2 class="abs section-title serif packages-title">FEATURED PACKAGES</h2>
  <div class="photo" style="left:112px;top:2848px;width:308px;height:240px;background:radial-gradient(circle at 55% 35%,#fff4d8 0%,#f6c877 18%,rgba(246,200,119,0) 45%),linear-gradient(180deg,#e8b66f 0%,#a87040 45%,#4a3322 75%,#2b1e16)" role="img" aria-label="Couple kissing at sunset"></div>
  <div class="photo" style="left:444px;top:2848px;width:308px;height:240px;background:radial-gradient(ellipse at 50% 65%,#e8dccd 0%,#9e8470 30%,rgba(158,132,112,0) 55%),linear-gradient(180deg,#8fbcd5 0%,#b9d3df 35%,#7b8a8a 60%,#4d4038)" role="img" aria-label="Couple embracing by the water"></div>
  <div class="photo" style="left:776px;top:2848px;width:308px;height:240px;background:radial-gradient(ellipse at 50% 65%,#f0ede6 0%,rgba(240,237,230,0) 25%),linear-gradient(180deg,#6b8a58 0%,#93a886 35%,#c0c6b1 55%,#6f7f5f 80%,#46523f)" role="img" aria-label="Couple under palm trees"></div>
  <div class="abs pkg-name" style="left:112px;top:3114px">WEDDING COLLECTION 1</div>
  <div class="abs pkg-name" style="left:444px;top:3114px">WEDDING COLLECTION 2</div>
  <div class="abs pkg-name" style="left:776px;top:3114px">WEDDING COLLECTION 3</div>
  <div class="abs pkg-price" style="left:112px;top:3144px">$1000</div>
  <div class="abs pkg-price" style="left:444px;top:3144px">$2000</div>
  <div class="abs pkg-price" style="left:776px;top:3144px">$3000</div>
</section>

<section class="testimonials">
  <h2 class="abs section-title serif testi-title">TESTIMONIALS</h2>
  <div class="arrow-btn" style="left:36px"><svg width="34" height="34" viewBox="0 0 34 34"><path d="M20 11 L14 17 L20 23" fill="none" stroke="var(--ink)" stroke-width="2.5"/></svg></div>
  <div class="arrow-btn" style="left:1130px"><svg width="34" height="34" viewBox="0 0 34 34"><path d="M14 11 L20 17 L14 23" fill="none" stroke="var(--ink)" stroke-width="2.5"/></svg></div>
  <article class="card" style="left:112px">
    <div class="avatar" style="background:radial-gradient(circle at 50% 40%,#d9b9a0,#8c6650 60%,#4a3a30)" role="img" aria-label="Client portrait"></div>
    <p>What!! I seriously cannot say enough good about Lumera! As a photographer, I have definitely hit some bumps in the road when it comes...</p>
    <div class="who">- Nora Ellison</div><div class="stars">★★★★★</div>
    <div class="quote">&rdquo;</div>
  </article>
  <article class="card" style="left:444px">
    <div class="avatar" style="background:radial-gradient(circle at 50% 40%,#cfae93,#6f5a4a 60%,#8fa36d)" role="img" aria-label="Client portrait"></div>
    <p>It has been an absolute joy working with Lumera as they built me a new website. The team at Lumera listened to all my needs for my website...</p>
    <div class="who">- Sam Porter</div><div class="stars">★★★★★</div>
    <div class="quote">&rdquo;</div>
  </article>
  <article class="card" style="left:776px">
    <div class="avatar" style="background:radial-gradient(circle at 50% 40%,#c9a487,#4a5670 60%,#dfe5ea)" role="img" aria-label="Client portrait"></div>
    <p>I cannot emphasize how grateful I am for these awesome peeps at Lumera! I wanted a very clean and simplistic website design...</p>
    <div class="who">- Miles Tandy</div><div class="stars">★★★★★</div>
    <div class="quote">&rdquo;</div>
  </article>
</section>

<footer class="footer-area">
  <div class="abs footer"></div>
  <div class="abs f-logo">LUMERA</div>
  <div class="abs to-top">GO TO TOP &nbsp;&#8593;</div>
  <div class="abs f-rule"></div>

  <div class="abs" style="left:112px;top:4046px;width:260px">
    <div class="f-head" style="margin-bottom:18px">CONTACT INFO</div>
    <div class="contact-row">
      <svg width="12" height="16" viewBox="0 0 12 16"><path d="M6 0C2.7 0 0 2.6 0 5.9 0 10 6 16 6 16s6-6 6-10.1C12 2.6 9.3 0 6 0zm0 8.2A2.3 2.3 0 1 1 6 3.6a2.3 2.3 0 0 1 0 4.6z" fill="var(--gold)"/></svg>
      <span>1450 Harbor Rd, Kahului,<br>HI 96732</span>
    </div>
    <div class="contact-row">
      <svg width="14" height="14" viewBox="0 0 14 14"><path d="M3 0l2 3-1.5 1.5c.8 2 2.4 3.6 4.5 4.5L9.5 7.5 14 9.5 13 13c-7 0-13-6-13-13z" fill="var(--gold)"/></svg>
      <span>+1 800 555 0142</span>
    </div>
    <div class="contact-row">
      <svg width="14" height="12" viewBox="0 0 14 12"><rect x="0" y="1" width="14" height="10" rx="1" fill="var(--gold)"/><path d="M0 2 L7 7 L14 2" fill="none" stroke="var(--footer)" stroke-width="1.3"/></svg>
      <span>contact@trylumera.example</span>
    </div>
  </div>

  <div class="abs" style="left:384px;top:4046px">
    <div class="f-head" style="margin-bottom:10px">BOOK A PHOTOGRAPHER</div>
    <ul class="f-list"><li>Marketplace</li><li>How It Works</li><li>About</li><li>Blog</li><li>FAQ</li><li>Terms of Service</li></ul>
  </div>

  <div class="abs" style="left:700px;top:4046px">
    <div class="f-head" style="margin-bottom:10px">COMPANY</div>
    <ul class="f-list"><li>About</li><li>Contact</li><li>Careers</li></ul>
  </div>

  <div class="abs" style="left:892px;top:4046px">
    <div class="f-head" style="margin-bottom:16px">FOLLOW US</div>
    <div class="f-social"><span></span><span></span><span></span><span></span></div>
  </div>

  <div class="abs bottom-rule"></div>
  <div class="abs copyright">© 2022 LUMERA &nbsp;|&nbsp; All Rights Reserved</div>
</footer>

</body>
</html>
```